Design a New Business Card for Our Company

We are looking for fresh, unique, and a modern business card that reflects our roots as digital marketing agency focused on SEM.

Industry/Entity Type

Marketing

Contact Information for Business Card

looking for very unique out of the box designs. clean and modern that compliments our logo

Requirements
Must have
• colors should match our logo
• Front should have name, address, email, and phone/fax of the person, phone/fax are the same number
• back should have our url

```html
<!DOCTYPE html>
<html lang="en">
<head>
<meta charset="utf-8">
<title>Brightwave Partners – Business Card</title>
<link rel="stylesheet" href="https://fonts.googleapis.com/css2?family=PT+Sans:wght@400;700&display=swap">
<style>
  :root {
    --page-bg: #ececec;
    --card-bg: #ffffff;
    --brand-blue: #4a8fd4;
    --back-blue: #5592ce;
    --text-grey: #8a8a8a;
    --rule-grey: #b9b9b9;
    --soft-blue: #d3e0f4;
    --white: #ffffff;
  }
  * { box-sizing: border-box; margin: 0; padding: 0; }
  html, body {
    width: 940px;
    height: 1200px;
    overflow: hidden;
    background: var(--page-bg);
    font-family: "PT Sans", "Myriad Pro", Arial, sans-serif;
  }
  .canvas {
    position: relative;
    width: 940px;
    height: 1200px;
  }
  .card {
    position: absolute;
    left: 212px;
    width: 515px;
    height: 296px;
    box-shadow: 0 2px 6px rgba(0,0,0,0.18);
  }
  .card--front { top: 254px; background: var(--card-bg); }
  .card--back  { top: 650px; background: var(--back-blue); }

  /* brand wordmark */
  .wordmark {
    position: absolute;
    display: flex;
    align-items: center;
    gap: 10px;
    font-weight: 700;
    line-height: 1;
  }
  .wordmark__dot {
    border-radius: 50%;
    flex: none;
  }
  .card--front .wordmark {
    left: 27px;
    top: 34px;
    font-size: 30px;
    color: var(--brand-blue);
  }
  .card--front .wordmark__dot {
    width: 22px; height: 22px;
    background: var(--brand-blue);
  }
  .card--back .wordmark {
    left: 0; right: 0;
    top: 124px;
    justify-content: center;
    font-size: 34px;
    color: var(--white);
  }
  .card--back .wordmark__dot {
    width: 24px; height: 24px;
    background: var(--white);
  }

  .accent-circle {
    position: absolute;
    left: 345px;
    top: 28px;
    width: 140px;
    height: 140px;
    border-radius: 50%;
    background: var(--soft-blue);
    opacity: 0.6;
  }

  .person {
    position: absolute;
    left: 25px;
    top: 127px;
  }
  .person__name {
    font-size: 17px;
    font-weight: 700;
    color: var(--brand-blue);
    line-height: 1.1;
  }
  .person__role {
    font-size: 13px;
    color: var(--text-grey);
    margin-top: 2px;
  }

  .contact-list {
    position: absolute;
    left: 25px;
    top: 172px;
    list-style: none;
  }
  .contact-list__item {
    display: flex;
    align-items: center;
    gap: 8px;
    font-size: 13.5px;
    color: var(--text-grey);
    line-height: 18px;
  }
  .contact-list__icon { width: 15px; height: 13px; flex: none; }

  .address {
    position: absolute;
    right: 23px;
    top: 224px;
    font-size: 13px;
    font-style: normal;
    color: var(--text-grey);
    text-align: right;
    line-height: 18px;
  }
  .card__rule {
    position: absolute;
    left: 27px;
    top: 270px;
    width: 248px;
    height: 1px;
    background: var(--rule-grey);
  }
  .site-link {
    position: absolute;
    right: 23px;
    top: 261px;
    font-size: 13px;
    color: var(--text-grey);
  }
  .site-link__label { color: var(--brand-blue); }

  .card--back .site-url {
    position: absolute;
    left: 24px;
    bottom: 20px;
    font-size: 12px;
    color: var(--white);
    letter-spacing: 0.2px;
  }
</style>
</head>
<body>
<main class="canvas">

  <section class="card card--front" aria-label="Business card front">
    <div class="wordmark"><span class="wordmark__dot"></span>Brightwave Partners</div>
    <div class="accent-circle" aria-hidden="true"></div>

    <div class="person">
      <p class="person__name">Owen Hartley</p>
      <p class="person__role">Owner</p>
    </div>

    <ul class="contact-list">
      <li class="contact-list__item">
        <svg class="contact-list__icon" viewBox="0 0 15 13" aria-label="Phone">
          <path d="M1 4 Q7.5 -1 14 4 L12 6 L10 4.5 L10 3.5 Q7.5 2.5 5 3.5 L5 4.5 L3 6 Z" fill="var(--brand-blue)"/>
          <rect x="3" y="6.5" width="9" height="6" rx="1" fill="var(--brand-blue)"/>
          <circle cx="7.5" cy="9.5" r="1.6" fill="#fff"/>
        </svg>
        555.201.348
      </li>
      <li class="contact-list__item">
        <svg class="contact-list__icon" viewBox="0 0 15 13" aria-label="Fax">
          <rect x="4" y="0.5" width="7" height="4" fill="none" stroke="var(--brand-blue)" stroke-width="1.2"/>
          <rect x="1" y="4.5" width="13" height="6" rx="1.2" fill="var(--brand-blue)"/>
          <rect x="4" y="8" width="7" height="4.5" fill="#fff" stroke="var(--brand-blue)" stroke-width="1"/>
        </svg>
        555.201.348
      </li>
      <li class="contact-list__item">
        <svg class="contact-list__icon" viewBox="0 0 15 13" aria-label="Email">
          <rect x="0.5" y="2" width="14" height="10" fill="var(--brand-blue)"/>
          <path d="M0.5 2 L7.5 8 L14.5 2" fill="none" stroke="#fff" stroke-width="1.2"/>
        </svg>
        hello@brightwavepartners.com
      </li>
    </ul>

    <address class="address">
      N. 14 Cedar Lane, Suite 200,<br>
      Tacoma, WA 98402
    </address>

    <div class="card__rule" aria-hidden="true"></div>
    <p class="site-link"><span class="site-link__label">Visit Us</span> www.brightwavepartners.com</p>
  </section>

  <section class="card card--back" aria-label="Business card back">
    <div class="wordmark"><span class="wordmark__dot"></span>Brightwave Partners</div>
    <p class="site-url">www.brightwavepartners.com</p>
  </section>

</main>
</body>
</html>
```